Professional & attention grabbing.

A business card design, front and back. I already have a logo I will attach, but I am open to something new as well.
Things to include:
Name:
Title:
Phone:
Email:
Wanting something that is professional but attention grabbing.
Also we do a lot of work using drones on natural gas pipelines (leading the future)if you want to include any of that. I'm open to ideas.
Target Market(s)
Natural gas transmission industry / greenhouse gas mitigation industry
Industry/Entity Type
Business
Colors
Designer to choose colors to be used in the design.
Look and feel
Each slider illustrates characteristics of the customer's brand and the style your logo design should communicate.

```html
<!DOCTYPE html>
<html lang="en">
<head>
<meta charset="utf-8">
<title>Kestrel Field Inspections – Business Card</title>
<link rel="stylesheet" href="https://fonts.googleapis.com/css2?family=Rajdhani:wght@500;600;700&display=swap">
<style>
  :root {
    --page-bg: #e6e3df;
    --card-bg: #f3f3f2;
    --card-edge: #d4d2cf;
    --ink-dark: #1f1f20;
    --band-dark: #161617;
    --brand-red: #9b1b20;
    --name-red: #b3262b;
    --text-light: #f2f2f2;
    --text-body: #3a3a3c;
  }
  * { margin: 0; padding: 0; box-sizing: border-box; }
  html, body {
    width: 1200px; height: 969px; overflow: hidden;
    background: var(--page-bg);
    font-family: "Rajdhani", sans-serif;
  }
  .card {
    position: absolute; left: 164px; top: 237px;
    width: 873px; height: 495px;
    background: var(--card-bg);
    border: 1px solid var(--card-edge);
    border-radius: 20px;
    overflow: hidden;
  }
  .brand {
    position: absolute; left: 53px; top: 74px;
    display: flex; align-items: center; gap: 18px;
  }
  .brand-square { width: 64px; height: 64px; background: var(--brand-red); }
  .brand-name {
    font-weight: 700; font-size: 44px; line-height: 1;
    color: var(--ink-dark); text-transform: uppercase; letter-spacing: 1px;
  }
  .identity-band {
    position: absolute; left: 0; top: 258px;
    width: 635px; height: 86px;
    background: var(--band-dark);
    padding: 8px 0 0 53px;
  }
  .person-name {
    font-weight: 700; font-size: 31px; line-height: 36px;
    color: var(--name-red); text-transform: uppercase; letter-spacing: 1px;
  }
  .person-title {
    font-weight: 500; font-size: 26px; line-height: 32px;
    color: var(--text-light);
  }
  .accent-band {
    position: absolute; left: 730px; top: 258px;
    width: 143px; height: 88px; background: var(--brand-red);
  }
  .accent-block {
    position: absolute; left: 642px; top: 258px;
    width: 82px; height: 88px; background: var(--band-dark);
  }
  .contacts {
    position: absolute; left: 56px; top: 372px;
    list-style: none;
  }
  .contacts li {
    display: flex; align-items: center; gap: 12px;
    height: 33px;
    font-weight: 500; font-size: 25px; color: var(--text-body);
  }
  .contacts svg { width: 20px; height: 20px; fill: var(--brand-red); flex: none; }
</style>
</head>
<body>
  <main class="card">
    <div class="brand">
      <span class="brand-square"></span>
      <span class="brand-name">Kestrel Field Inspections</span>
    </div>

    <section class="identity-band">
      <p class="person-name">Dana Ortiz</p>
      <p class="person-title">CEO/Founder</p>
    </section>
    <div class="accent-block"></div>
    <div class="accent-band"></div>

    <ul class="contacts">
      <li>
        <svg viewBox="0 0 24 24" aria-hidden="true"><path d="M6.6 10.8a15 15 0 0 0 6.6 6.6l2.2-2.2a1 1 0 0 1 1-.25 11.4 11.4 0 0 0 3.6.57 1 1 0 0 1 1 1V20a1 1 0 0 1-1 1A17 17 0 0 1 3 4a1 1 0 0 1 1-1h3.5a1 1 0 0 1 1 1c0 1.25.2 2.45.57 3.6a1 1 0 0 1-.25 1z"/></svg>
        <span>555 204 7316</span>
      </li>
      <li>
        <svg viewBox="0 0 24 24" aria-hidden="true"><path d="M2 5h20v14H2z M3.5 6.5 12 12.5l8.5-6z" fill-rule="evenodd"/></svg>
        <span>dana@kestrelfield.com</span>
      </li>
      <li>
        <svg viewBox="0 0 24 24" aria-hidden="true"><circle cx="12" cy="12" r="10"/><path d="M2 12h20M12 2c3 3 3 17 0 20M12 2c-3 3-3 17 0 20" stroke="#f3f3f2" stroke-width="1.6" fill="none"/></svg>
        <span>www.kestrelfield.com</span>
      </li>
    </ul>
  </main>
</body>
</html>
```